Digital One Pager for Consulting Practice

I would like the essence of the content in my ppt consolidated into a one-pager. The one-pager will mainly be sent via email as a pdf and intended to excite and invite new clients and establish the credibility of my boutique high-end consulting firm. Infographics and symbols would be a plus. The target client should view the firm as providing premeir service. The client is getting a thought partner.

Target Market(s)

Large Medical Device Manufacturer Executives, Early-Stage Medical Device Manufacturer Executives, Partners at VC Firms

Industry/Entity Type

Medical Equipment

Colors
0355a3
f37122

Requirements
Must have
• Please match the color scheme in ppt. Please use the existing logo. I am very open to better graphics on the process. My photo does not need to be on the digital flyer. Hyper link to the website and email is needed.
Nice to have
• Infographics

```html
<!DOCTYPE html>
<html lang="en">
<head>
<meta charset="utf-8">
<title>Kestrel Advisory – One Pager</title>
<link rel="stylesheet" href="https://fonts.googleapis.com/css2?family=Oswald:wght@400;500;600;700&family=Montserrat:wght@400;500;600;700&display=swap">
<style>
  :root{
    --navy:#141a2e;
    --navy-soft:#232a42;
    --orange:#e8472b;
    --orange-soft:#f07a5f;
    --ink:#1d2233;
    --grey:#6b6f7a;
    --grey-light:#c9cbd1;
    --paper:#ffffff;
    --backdrop:#e6e6e8;
  }
  *{box-sizing:border-box;margin:0;padding:0}
  html,body{width:920px;height:1200px;overflow:hidden;background:var(--backdrop)}
  body{font-family:"Montserrat",Arial,sans-serif;color:var(--ink)}
  .flyer{position:relative;width:920px;height:1200px;background:var(--paper);overflow:hidden}

  .hero-photo{position:absolute;left:0;top:0;width:920px;height:340px;
    background:linear-gradient(180deg,#ffffff 0%,#f1f2f4 14%,#c7ccd3 40%,#8d96a3 70%,#a9b0ba 100%)}
  .hero-fade{position:absolute;left:0;top:0;width:920px;height:70px;background:linear-gradient(180deg,#fff 40%,rgba(255,255,255,0))}

  .brand{position:absolute;top:18px;left:470px;display:flex;align-items:center;gap:10px}
  .brand-dot{width:16px;height:16px;border-radius:50%;background:var(--orange)}
  .brand-name{font-family:"Oswald",Arial,sans-serif;font-weight:600;font-size:34px;letter-spacing:2px;color:var(--navy);line-height:1}

  .headline{position:absolute;left:0;top:372px;width:455px;text-align:center;font-family:"Oswald",Arial,sans-serif}
  .headline .kicker{color:var(--orange);font-weight:600;font-size:31px;line-height:1.15}
  .headline .main{color:var(--navy);font-weight:700;font-size:40px;line-height:1.15;letter-spacing:.5px}
  .headline .sub{color:var(--navy);font-weight:500;font-size:30px;line-height:1.2}

  .side-panel{position:absolute;left:0;top:585px;width:455px;height:603px;background:var(--navy);color:#fff;padding:26px 30px 0 30px}
  .section-title{display:flex;align-items:center;gap:10px;font-family:"Oswald",Arial,sans-serif;font-weight:600;font-size:19px;letter-spacing:.5px;text-transform:uppercase}
  .section-title .badge{width:30px;height:30px;border-radius:50%;border:2px solid currentColor;display:flex;align-items:center;justify-content:center}
  .side-panel .intro{font-size:12.5px;line-height:1.55;margin:14px 0 16px;color:#e8e9ee}
  .ticks{list-style:none;font-size:12.5px;line-height:1.9;color:#e8e9ee;margin-bottom:26px}
  .ticks li::before{content:"";display:inline-block;width:7px;height:7px;border-radius:50%;background:var(--orange);margin-right:10px;vertical-align:1px}
  .services{display:grid;grid-template-columns:1fr 1fr;gap:22px 22px;margin-top:16px}
  .service h4{color:var(--orange);font-weight:600;font-size:13px;margin-bottom:5px}
  .service ul{list-style:none;font-size:12px;line-height:1.6;color:#e8e9ee}
  .service li::before{content:"";display:inline-block;width:6px;height:6px;border-radius:50%;background:var(--orange);margin-right:8px;vertical-align:1px}

  .right-col{position:absolute;left:478px;top:350px;width:420px}
  .heading-orange{display:flex;align-items:center;gap:9px;font-family:"Oswald",Arial,sans-serif;color:var(--orange);font-weight:600;font-size:20px;text-transform:uppercase}
  .heading-orange .badge{width:28px;height:28px;border-radius:50%;background:var(--navy);display:flex;align-items:center;justify-content:center}
  .offer{margin:12px 0 0 18px}
  .offer h3{font-size:13.5px;font-weight:700;color:var(--navy);margin-bottom:4px}
  .offer h3::before{content:"";display:inline-block;width:8px;height:8px;background:var(--orange);border-radius:50%;margin-right:8px}
  .offer ul{list-style:none;font-size:12px;line-height:1.55;color:var(--grey);margin:0 0 14px 16px}
  .offer li::before{content:"•";color:var(--orange);margin-right:7px}

  .process-title{margin-top:16px}
  .process{position:relative;height:150px;margin-top:14px}
  .process svg{position:absolute;left:0;top:0}
  .step-label{position:absolute;top:92px;width:96px;text-align:center;font-size:11.5px;font-weight:700;color:var(--navy);line-height:1.25}

  .differentiators{position:absolute;left:478px;top:930px;width:200px;height:40px;background:var(--navy);color:#fff;font-family:"Oswald",Arial,sans-serif;font-weight:600;font-size:20px;letter-spacing:1px;display:flex;align-items:center;justify-content:center}
  .cycle{position:absolute;left:690px;top:862px}

  .contact{position:absolute;left:478px;top:1045px;width:420px}
  .contact h2{font-family:"Oswald",Arial,sans-serif;color:var(--orange);font-weight:600;font-size:24px;margin-bottom:8px}
  .contact-grid{display:grid;grid-template-columns:170px 1fr;gap:6px 10px;font-size:12.5px;color:var(--navy)}
  .contact-item{display:flex;align-items:center;gap:7px}
  .contact-item a{color:var(--navy);text-decoration:none}
  .contact-item .ico{width:18px;height:18px;border-radius:50%;background:var(--orange);display:flex;align-items:center;justify-content:center}

  .partner-row{position:absolute;left:478px;top:1148px;display:flex;gap:14px;align-items:center}
  .partner{height:18px;background:var(--grey-light);border-radius:2px}
  .partner.blue{background:#3b6fb4}

  .base-stripe{position:absolute;left:0;bottom:0;width:920px;height:12px;background:var(--orange)}
</style>
</head>
<body>
<main class="flyer">
  <div class="hero-photo" role="img" aria-label="Photograph of four colleagues discussing around a meeting table with a laptop in a bright office"></div>
  <div class="hero-fade"></div>

  <div class="brand">
    <span class="brand-dot"></span>
    <span class="brand-name">KESTREL ADVISORY</span>
  </div>

  <header class="headline">
    <p class="kicker">Extensive Experience</p>
    <p class="main">EFFICIENT PROCESS</p>
    <p class="sub">VALUED NETWORK</p>
  </header>

  <section class="side-panel">
    <h2 class="section-title">
      <span class="badge"><svg width="14" height="14" viewBox="0 0 14 14"><circle cx="7" cy="5" r="3" fill="none" stroke="#fff" stroke-width="1.6"/><path d="M2 13c1-3 3-4 5-4s4 1 5 4" fill="none" stroke="#fff" stroke-width="1.6"/></svg></span>
      Experience
    </h2>
    <p class="intro">Over a decade @FDA (Former Deputy Division Director)<br>
      Expertise: Cardiovascular, Ophthalmology, General Hospital, Infection Control, Dental, Anesthesia, Respiratory<br>
      Vice President Regulatory Affairs / Quality Assurance @Halvorsen Group (Fortune 150 Company)</p>
    <ul class="ticks">
      <li>Initiated reorganization of department</li>
      <li>Led major compliance effort</li>
      <li>Successful FDA inspection (no observations)</li>
    </ul>

    <h2 class="section-title">
      <span class="badge"><svg width="14" height="14" viewBox="0 0 14 14"><circle cx="7" cy="7" r="2.5" fill="#fff"/><path d="M7 1v2M7 11v2M1 7h2M11 7h2M2.8 2.8l1.4 1.4M9.8 9.8l1.4 1.4M2.8 11.2l1.4-1.4M9.8 4.2l1.4-1.4" stroke="#fff" stroke-width="1.5"/></svg></span>
      Services
    </h2>
    <div class="services">
      <div class="service"><h4>Regulatory Strategy</h4><ul><li>RA/QA Organizational Structure</li><li>Regulatory Pathway</li></ul></div>
      <div class="service"><h4>FDA Communications</h4><ul><li>Deficiency Response</li><li>Application Review</li></ul></div>
      <div class="service"><h4>Interim Executive Leadership</h4><ul><li>Compliance Remediation</li><li>Accelerated Product Registration</li></ul></div>
      <div class="service"><h4>Training</h4><ul><li>FDA Communication</li><li>MDR Reporting</li></ul></div>
    </div>
  </section>

  <section class="right-col">
    <h2 class="heading-orange">
      <span class="badge"><svg width="14" height="14" viewBox="0 0 14 14"><path d="M3 7l3 3 5-6" fill="none" stroke="#fff" stroke-width="2"/></svg></span>
      Experience to provide
    </h2>
    <div class="offer">
      <h3>Executive Application Review</h3>
      <ul>
        <li>Examples include: (Pre-)Submission, IDE, 510(k), 513(g), PMA, Refuse to Accept, Hold letter</li>
        <li>Troubleshooting</li>
      </ul>
      <h3>Strategic Advice &amp; Diligence to Investors</h3>
      <ul>
        <li>Validate &amp; Verify Founder Milestones</li>
        <li>Diligence portfolio company Regulatory and Quality systems</li>
      </ul>
    </div>

    <h2 class="heading-orange process-title">Efficient Process</h2>
    <div class="process">
      <svg width="420" height="90" viewBox="0 0 420 90">
        <line x1="48" y1="44" x2="372" y2="44" stroke="#141a2e" stroke-width="4"/>
        <g>
          <circle cx="48" cy="44" r="36" fill="none" stroke="#141a2e" stroke-width="7"/>
          <circle cx="48" cy="44" r="26" fill="#e8472b"/>
          <path d="M39 34c2-2 4-1 5 1l1 3c0 2-2 2-2 3 1 3 3 5 6 6 1 0 1-2 3-2l3 1c2 1 3 3 1 5-3 3-8 2-12-2s-7-10-5-15z" fill="#fff"/>
        </g>
        <g>
          <circle cx="156" cy="44" r="36" fill="none" stroke="#e8472b" stroke-width="7"/>
          <circle cx="156" cy="44" r="26" fill="#141a2e"/>
          <path d="M142 54l9-14 5 7 4-5 8 12z" fill="#e8472b"/>
        </g>
        <g>
          <circle cx="264" cy="44" r="36" fill="none" stroke="#141a2e" stroke-width="7"/>
          <circle cx="264" cy="44" r="26" fill="#e8472b"/>
          <text x="264" y="54" text-anchor="middle" font-family="Oswald, sans-serif" font-weight="700" font-size="28" fill="#fff">?</text>
        </g>
        <g>
          <circle cx="372" cy="44" r="36" fill="none" stroke="#e8472b" stroke-width="7"/>
          <circle cx="372" cy="44" r="26" fill="#141a2e"/>
          <path d="M361 45l7 7 14-15" fill="none" stroke="#e8472b" stroke-width="4"/>
        </g>
      </svg>
      <p class="step-label" style="left:0">Exploratory Call</p>
      <p class="step-label" style="left:108px">Regulatory Landscape</p>
      <p class="step-label" style="left:216px">Problem Statement</p>
      <p class="step-label" style="left:324px">Review &amp; Align on Deliverables</p>
    </div>
  </section>

  <div class="differentiators">DIFFERENTIATORS</div>

  <svg class="cycle" width="210" height="175" viewBox="0 0 210 175" role="img" aria-label="Cycle of expertise, network and process feeding leverage">
    <path d="M62 48 A70 70 0 0 1 148 48" fill="none" stroke="#c9cbd1" stroke-width="4"/>
    <path d="M168 82 A70 70 0 0 1 128 150" fill="none" stroke="#c9cbd1" stroke-width="4"/>
    <path d="M82 150 A70 70 0 0 1 42 82" fill="none" stroke="#c9cbd1" stroke-width="4"/>
    <circle cx="105" cy="34" r="30" fill="#eeeff1" stroke="#9a9ea8" stroke-width="3"/>
    <circle cx="170" cy="135" r="30" fill="#eeeff1" stroke="#9a9ea8" stroke-width="3"/>
    <circle cx="40" cy="135" r="30" fill="#eeeff1" stroke="#9a9ea8" stroke-width="3"/>
    <text x="105" y="37" text-anchor="middle" font-family="Montserrat, sans-serif" font-weight="700" font-size="8.5" fill="#141a2e">EXPERTISE</text>
    <text x="170" y="138" text-anchor="middle" font-family="Montserrat, sans-serif" font-weight="700" font-size="8.5" fill="#141a2e">NETWORK</text>
    <text x="40" y="138" text-anchor="middle" font-family="Montserrat, sans-serif" font-weight="700" font-size="8.5" fill="#141a2e">PROCESS</text>
    <text x="105" y="102" text-anchor="middle" font-family="Oswald, sans-serif" font-weight="600" font-size="14" fill="#e8472b">LEVERAGE</text>
  </svg>

  <section class="contact">
    <h2>Contact us</h2>
    <div class="contact-grid">
      <div class="contact-item">
        <span class="ico"><svg width="10" height="10" viewBox="0 0 10 10"><path d="M2 1c1-1 2 0 2 1l0 1c0 1-1 1-1 1 0 1 2 3 3 3 0 0 0-1 1-1h1c1 0 2 1 1 2-2 2-4 1-6-1S1 2 2 1z" fill="#fff"/></svg></span>
        <span>555.014.2290</span>
      </div>
      <div class="contact-item">
        <span class="ico"><svg width="10" height="10" viewBox="0 0 10 10"><circle cx="5" cy="5" r="4" fill="none" stroke="#fff" stroke-width="1.2"/><path d="M1 5h8M5 1c2 2 2 6 0 8M5 1c-2 2-2 6 0 8" fill="none" stroke="#fff" stroke-width="1"/></svg></span>
        <a href="https://www.kestreladvisory.com">www.kestreladvisory.com</a>
      </div>
      <div class="contact-item">
        <span class="ico"><svg width="10" height="10" viewBox="0 0 10 10"><rect x="1" y="2" width="8" height="6" fill="none" stroke="#fff" stroke-width="1.2"/><path d="M1 2l4 3 4-3" fill="none" stroke="#fff" stroke-width="1.2"/></svg></span>
        <a href="mailto:info@kestreladvisory.com">info@kestreladvisory.com</a>
      </div>
    </div>
  </section>

  <div class="partner-row" aria-hidden="true">
    <span class="partner" style="width:38px"></span>
    <span class="partner" style="width:34px"></span>
    <span class="partner" style="width:40px"></span>
    <span class="partner" style="width:70px"></span>
    <span class="partner" style="width:70px"></span>
    <span class="partner blue" style="width:28px"></span>
  </div>

  <div class="base-stripe"></div>
</main>
</body>
</html>
```